Consulting company business cards

We have a base design, but would be willing to update. We have a new logo/"tag" that needs to be added. Current business card design is attached for reference into our "style."

Industry/Entity Type

Business

Contact Information for Business Card

Should contain name and title, office number, mobile number if appropriate, e-mail, website, physical address, and company logo.

Font styles to use
Other font styles liked:
• See current card design on KorvandBCard

Colors
0455a3
85acd3
aaaaaa

Requirements
Must have
• Our colors are navy blue, gray, and a lighter blue
Nice to have
• Design that I can easily drop in new names/titles as we hire employees.

```html
<!DOCTYPE html>
<html lang="en">
<head>
<meta charset="utf-8">
<title>Quillmore Business Cards</title>
<link rel="stylesheet" href="https://fonts.googleapis.com/css2?family=Arimo:wght@400;700&display=swap">
<style>
  :root {
    --navy: #0455a3;
    --light-blue: #85acd3;
    --gray: #aaaaaa;
    --card: #141516;
    --card-edge: #1d1e20;
    --backdrop: #3b3431;
    --white: #f2f2f2;
    --mark: #2a2b2d;
    --divider: #3a3c40;
  }
  * { margin: 0; padding: 0; box-sizing: border-box; }
  html, body { width: 1200px; height: 864px; overflow: hidden; }
  body {
    background: var(--backdrop);
    font-family: "Arimo", Arial, sans-serif;
    position: relative;
  }
  .card {
    position: absolute;
    top: 278px;
    width: 540px;
    height: 309px;
    background: var(--card);
    border: 1px solid var(--card-edge);
    box-shadow: 0 12px 30px rgba(0,0,0,.45);
  }
  .card--front { left: 36px; }
  .card--back { left: 624px; }

  /* Front */
  .brand {
    position: absolute;
    left: 54px;
    top: 88px;
    display: flex;
    align-items: center;
    gap: 14px;
  }
  .brand__name {
    font-weight: 400;
    font-size: 50px;
    letter-spacing: 1px;
    color: var(--gray);
    line-height: 1;
  }
  .brand__mark {
    width: 30px; height: 30px;
    border-radius: 50%;
    background: var(--mark);
  }
  .tagline {
    position: absolute;
    left: 55px;
    top: 150px;
    font-size: 14px;
    letter-spacing: 2px;
    color: var(--gray);
    text-transform: uppercase;
  }
  .front-web {
    position: absolute;
    left: 55px;
    top: 210px;
    font-size: 14px;
    letter-spacing: 5px;
    color: var(--gray);
  }

  /* Back */
  .emblem {
    position: absolute;
    left: 60px;
    top: 60px;
    width: 190px;
    height: 190px;
    display: flex;
    align-items: center;
    justify-content: center;
  }
  .emblem__disc {
    width: 150px; height: 150px;
    border-radius: 50%;
    background: var(--light-blue);
  }
  .divider {
    position: absolute;
    left: 282px;
    top: 62px;
    width: 1px;
    height: 186px;
    background: var(--divider);
  }
  .contact {
    position: absolute;
    left: 306px;
    top: 66px;
    color: var(--white);
  }
  .contact__name { font-size: 20px; color: var(--navy); line-height: 1.1; }
  .contact__title { font-size: 15px; color: var(--light-blue); margin-bottom: 14px; }
  .contact__address { font-size: 14px; line-height: 1.25; margin-bottom: 10px; }
  .contact__list { list-style: none; font-size: 14px; }
  .contact__list li { display: flex; align-items: center; gap: 8px; height: 20px; }
  .contact__icon { width: 12px; height: 12px; flex: none; }
</style>
</head>
<body>
  <section class="card card--front" aria-label="Card front">
    <div class="brand">
      <span class="brand__name">Quillmore</span>
      <span class="brand__mark"></span>
    </div>
    <p class="tagline">A Cloud Consulting Company</p>
    <p class="front-web">www.quillmore.io</p>
  </section>

  <section class="card card--back" aria-label="Card back">
    <div class="emblem" role="img" aria-label="Company emblem area">
      <span class="emblem__disc"></span>
    </div>
    <div class="divider"></div>
    <div class="contact">
      <p class="contact__name">Renatakorvand</p>
      <p class="contact__title">Office Manager</p>
      <p class="contact__address">1180 W 54th ST<br>Fairbrook Indiana 46010</p>
      <ul class="contact__list">
        <li>
          <svg class="contact__icon" viewBox="0 0 12 12"><path fill="#0455a3" d="M2 1h3l1 3-1.5 1a6 6 0 0 0 2.5 2.5L8 6l3 1v3a1 1 0 0 1-1 1A9 9 0 0 1 1 2a1 1 0 0 1 1-1z"/></svg>
          555.014.2910
        </li>
        <li>
          <svg class="contact__icon" viewBox="0 0 12 12"><rect x="1" y="4" width="10" height="6" fill="#0455a3"/><rect x="3" y="1" width="6" height="3" fill="#0455a3"/></svg>
          555.014.2971
        </li>
        <li>
          <svg class="contact__icon" viewBox="0 0 12 12"><rect x="1" y="2.5" width="10" height="7" fill="#0455a3"/><path d="M1 2.5l5 4 5-4" fill="none" stroke="#141516" stroke-width="1"/></svg>
          rkorvand@quillmore.io
        </li>
        <li>
          <svg class="contact__icon" viewBox="0 0 12 12"><circle cx="6" cy="6" r="5" fill="#0455a3"/><path d="M1 6h10M6 1c2 2 2 8 0 10M6 1c-2 2-2 8 0 10" fill="none" stroke="#141516" stroke-width=".8"/></svg>
          www.quillmore.io
        </li>
      </ul>
    </div>
  </section>
</body>
</html>
```